Agrarhandel benötigt Homepage
Zielgruppe
Wir sind ein Agrarhandel mit einem Warenumschlagslager im Sinne eines klassischen Einzelhandels und vertreiben Produkte an Landwirte.
Wir vertreiben folgende Hauptproduktgruppen:
Einzelfuttermittel
wie z.B. Sojaexktraktionsschrot. Die einzelnen Produkte könnten z.B. wie die Futtermittel auf folgender Seite dargestellt werden (https://www.kornprobe-beispiel.eu/de/produkt/trelomixan)
Mischfuttermittel
Hier bieten wir unseren Kunden an, individuelles Mischfutter auf Basis unserer Einzelfuttermittel herzustellen.
Weitere Details und weitere Produktbereiche habe ich in einer Powerpoint-Übersicht dargestellt.
Neben diesen Produkten wollen wir uns als Familienunternehmen selbst vorstellen. Zudem betreiben wir in unserer Familie zusätzlich einen Milchviehbetrieb den wir ebenfalls hervorheben möchten, da wir unseren Kunden gegenüber einerseits als Zulieferer aber auch als Kollege auftreten wollen.
Einzelfuttermittel: Hier können wir durch unsere Unabhängigkeit punkten, da wir nicht abhängig von bestimmten Lieferanten sind und dementsprechend unabhängig beraten können. Wir untersuchen im Vergleich zu unseren Wettbewerben die Qualität der Futtermittel bis ins Detail und können daher eine Transparenz bieten, die Konkurrenten in der Regel nicht bieten können. Unser Warenumschlagsplatz mit moderner Technik ermöglicht es uns äußerst kosteneffizient die Waren umschlagen und ausliefern zu können.
Mischfuttermittel: Auf Basis der vorhandenen Einzelfuttermittel stellen wir je nach Kundenwunsch individuelle Mischfutter her. Wir arbeiten mit offenen Deklarationen, sodass unsere Kunden jederzeit nachvollziehen können, ob auch die Einzelfuttermittel verwendet wurden, die sie bestellt haben und keine billigen Ersatzprodukte verwendet wurden.
Zudem sind wir BT und HUPA zertifiziert. Die aktuellen für unser Unternehmen ausgestellten Zertifikate müssen für unsere Kunden als Download zur Verfügung stehen. Statt dem HUPA-Logo bitte das ..
Aufgabenstellung
Wir möchten gerne ein zeitgemäße Homepage, jedoch muss auch berücksichtigt werden, dass unsere Kunden eher konservativ denken.

```html
<!DOCTYPE html>
<html lang="de">
<head>
<meta charset="utf-8">
<title>Albtal Landhandel – Landwirt</title>
<link href="https://fonts.googleapis.com/css2?family=Inter:wght@400;600;700&family=Outfit:wght@400;500;700;800&family=Jost:wght@500&display=swap" rel="stylesheet">
<style>
:root{
  --orange:#f9ab25;
  --orange-soft:#fab438;
  --green:#126952;
  --green-text:#1a6b50;
  --brown:#3b2314;
  --ink:#141414;
  --white:#ffffff;
}
*{margin:0;padding:0;box-sizing:border-box}
html,body{width:734px;height:1200px;overflow:hidden;background:var(--white)}
body{position:relative;font-family:"Outfit",sans-serif;color:var(--ink)}
.abs{position:absolute}

/* header */
.header-strip{left:0;top:0;width:43px;height:70px;background:var(--orange)}
.brand{left:43px;top:0;width:119px;height:70px;background:var(--white);display:flex;flex-direction:column;align-items:center;justify-content:flex-end;padding-bottom:6px}
.brand-dot{width:22px;height:22px;border-radius:50%;background:var(--orange);margin-bottom:7px}
.brand-name{font-family:"Outfit",sans-serif;font-weight:700;font-size:9.5px;color:var(--green);letter-spacing:.1px}
.header-bar{left:162px;top:0;width:572px;height:70px;background:var(--green)}
.nav{left:266px;top:32px;width:414px;display:flex;justify-content:space-between;font-family:"Outfit",sans-serif;font-weight:700;font-size:8.8px;color:var(--white);white-space:nowrap}
.nav .active{color:var(--orange)}
.search{left:696px;top:31px}

/* backgrounds */
.bands{left:0;top:0}

/* intro */
.intro{left:117px;top:110px;width:498px;height:122px;background:var(--orange-soft);border:1px solid #ffd58a;border-radius:9px;padding:12px 8px;font-family:"Inter",sans-serif;font-weight:600;font-size:12.2px;line-height:14.8px;text-align:center;color:var(--ink)}

/* features */
.feature{width:126px;text-align:center;top:314px}
.feature svg{display:block;margin:0 auto}
.feature h3{font-family:"Outfit",sans-serif;font-weight:500;font-size:11.5px;margin-top:8px}
.feature p{font-family:"Outfit",sans-serif;font-weight:400;font-size:10.3px;line-height:17.3px;margin-top:12px}

/* why */
.why-title{left:178px;top:525px;font-family:"Inter",sans-serif;font-weight:400;font-size:18.5px;color:var(--white)}
.why-lead{left:176px;top:560px;width:240px;font-family:"Inter",sans-serif;font-size:5.6px;line-height:7px;color:var(--white)}
.why-item{width:66px;font-family:"Inter",sans-serif;color:var(--white)}
.why-item .dot{position:absolute;left:-19px;top:0;width:12px;height:12px;border-radius:50%;background:var(--orange)}
.why-item h4{font-size:5.8px;font-weight:600;margin-bottom:5px}
.why-item p{font-size:5.4px;line-height:6.6px}
.why-btn{left:322px;top:689px;width:56px;height:15px;border-radius:8px;background:var(--orange)}
.photo-frame{left:453px;top:527px;width:249px;height:169px;border-radius:6px;background:var(--orange)}
.photo{left:444px;top:535px;width:250px;height:170px;background:linear-gradient(160deg,#e9b26a 0%,#c98a3e 35%,#8a5a2a 70%,#4a3020 100%)}

/* certificates */
.badge{border-radius:4px}
.badge-hupa{left:62px;top:836px;width:82px;height:80px;background:#5cab3a;border:3px solid #dfeed6}
.badge-bt{left:254px;top:836px;width:65px;height:74px;background:#ffffff;border:1.5px solid #2b7cc4}
.badge-bt::after{content:"";position:absolute;left:14px;top:10px;width:34px;height:34px;border-radius:50%;background:#2b7cc4}
.und{left:186px;top:861px;font-family:"Inter",sans-serif;font-weight:600;font-size:12px}
.zert{left:142px;top:912px;font-family:"Jost",sans-serif;font-weight:500;font-size:22px;letter-spacing:.5px}
.download{left:445px;top:861px;width:228px;height:63px;border-radius:32px;background:var(--orange);box-shadow:4px 4px 6px rgba(0,0,0,.25);display:flex;align-items:center;justify-content:center;text-align:center;font-family:"Outfit",sans-serif;font-weight:800;font-size:18px;line-height:20px;color:var(--ink);letter-spacing:.6px}
.band-orange{left:0;top:949px;width:734px;height:31px;background:var(--orange)}

/* footer */
.foot-col{top:1004px;font-family:"Outfit",sans-serif;font-size:10.7px;line-height:17.3px;color:var(--green-text);font-weight:500;white-space:nowrap}
.foot-col h5{font-weight:800;font-size:13.5px;color:var(--orange);line-height:18px;margin-bottom:2px}
.contact li{list-style:none;display:flex;align-items:center;gap:5px}
.contact svg{flex:none}
.mini-hupa{left:634px;top:1026px;width:41px;height:40px;background:#5cab3a;border:2px solid #dfeed6;border-radius:3px}
.mini-bt{left:682px;top:1028px;width:33px;height:38px;background:#fff;border:1px solid #2b7cc4}
.mini-bt::after{content:"";position:absolute;left:8px;top:5px;width:16px;height:16px;border-radius:50%;background:#2b7cc4}
.legal{left:20px;top:1099px;width:694px;text-align:center;font-family:"Outfit",sans-serif;font-weight:500;font-size:10.2px;line-height:17.3px;color:var(--ink)}
.copy-bar{left:0;top:1169px;width:734px;height:31px;background:var(--orange);display:flex;align-items:center;justify-content:center;font-family:"Inter",sans-serif;font-weight:600;font-size:6.6px;padding-top:10px}
</style>
</head>
<body>

<svg class="abs bands" width="734" height="1200" viewBox="0 0 734 1200" aria-hidden="true">
  <polygon points="0,84 734,84 734,237 0,313" fill="#f9ab25"/>
  <path d="M94,357 L622,292 Q648,290 648,316 L648,447 Q648,473 622,473 L120,473 Q94,473 94,447 L94,383 Q94,359 118,355 Z" fill="#f9ab25"/>
  <polygon points="0,494 734,494 734,779 0,683" fill="#3b2314"/>
  <polygon points="0,742 734,779 734,800 0,810" fill="#f9ab25"/>
</svg>

<header>
  <div class="abs header-strip"></div>
  <div class="abs brand"><span class="brand-dot"></span><span class="brand-name">ALBTAL LANDHANDEL</span></div>
  <div class="abs header-bar"></div>
  <nav class="abs nav">
    <span class="active">LANDWIRT</span><span>GESCHÄFTSPARTNER</span><span>LIEFERANTEN</span><span>PRODUKTE ⌄</span><span>FIRMENPRÄSENTATION</span>
  </nav>
  <svg class="abs search" width="14" height="14" viewBox="0 0 14 14" aria-label="Suche"><circle cx="5.5" cy="5.5" r="4.3" fill="none" stroke="#fff" stroke-width="1.4"/><line x1="8.6" y1="8.6" x2="13" y2="13" stroke="#fff" stroke-width="1.6"/></svg>
</header>

<section>
  <p class="abs intro">Excepteur sint occaecat cupidatat non proident, sunt in culpa qExcepteur sint occaecat cupidatat non proident, sunt in culpa qui officia deserunt mollit anim id esExcepteur sint occaecat cupidatat non proident, sunt in culpa qui officia deserunt mollit anim id esExcepteur sint occaecat cupidatat non proident, sunt in culpa qui officia deserunt mollit anim id Excepteur sint occaecat cupidatat non proident, sunt in culpa qui officia deserunt mollit anim id es officia deserunt mollit anim id es</p>

  <div class="abs feature" style="left:110px">
    <svg width="28" height="28" viewBox="0 0 28 28"><path d="M14 2 L25 6 V13 Q25 22 14 27 Q3 22 3 13 V6 Z" fill="#111"/><path d="M14 20 V12 M14 16 Q9 15 9 10 Q13 11 14 16 Q15 11 19 10 Q19 15 14 16" stroke="#fff" stroke-width="1.5" fill="none"/></svg>
    <h3>Lorem Ipsum</h3>
    <p>Excepteur Sint Occaecat Cupidatat Non Proident, Sunt In Excepteur Sint Occaecat Cupidatat Non</p>
  </div>
  <div class="abs feature" style="left:241px">
    <svg width="28" height="32" viewBox="0 0 28 32"><polygon points="8,18 4,30 9,27 12,31 14,22" fill="#111"/><polygon points="20,18 24,30 19,27 16,31 14,22" fill="#111"/><circle cx="14" cy="12" r="11" fill="#111"/><circle cx="14" cy="12" r="7.5" fill="none" stroke="#fff" stroke-width="1.3"/><polyline points="10.5,12 13,14.5 17.5,9.5" fill="none" stroke="#fff" stroke-width="1.8"/></svg>
    <h3 style="margin-top:4px">Lorem Ipsum</h3>
    <p>Excepteur Sint Occaecat Cupidatat Non Proident, Sunt In Excepteur Sint Occaecat Cupidatat Non</p>
  </div>
  <div class="abs feature" style="left:377px">
    <svg width="26" height="26" viewBox="0 0 26 26"><circle cx="13" cy="13" r="12.5" fill="#111"/><path d="M13 19 Q6 18 6 11 Q11 11 13 17 Q15 11 20 11 Q20 18 13 19 Z" fill="#f9ab25"/></svg>
    <h3 style="margin-top:10px">Lorem Ipsum</h3>
    <p style="margin-top:10px">Excepteur Sint Occaecat Cupidatat Non Proident, Sunt In Excepteur Sint Occaecat Cupidatat Non</p>
  </div>
  <div class="abs feature" style="left:508px">
    <svg width="32" height="30" viewBox="0 0 32 30"><path d="M16 2 L22 4 V8 Q22 12 16 14 Q10 12 10 8 V4 Z" fill="none" stroke="#111" stroke-width="1.3"/><path d="M2 16 L9 13 L16 18 L23 13 L30 16 L26 24 L20 28 L12 28 L6 24 Z" fill="#111"/></svg>
    <h3 style="margin-top:6px">Lorem Ipsum</h3>
    <p style="margin-top:10px">Excepteur Sint Occaecat Cupidatat Non Proident, Sunt In Excepteur Sint Occaecat Cupidatat Non</p>
  </div>
</section>

<section>
  <h2 class="abs why-title">Warum Uns Wählen?</h2>
  <p class="abs why-lead">Excepteur sint occaecat cupidatat non proident, sunt in culpa qui officia deserunt mollit anim id es</p>
  <div class="abs why-item" style="left:195px;top:589px"><span class="dot"></span><h4>Lorem Ipsum</h4><p>Excepteur sint occaecat cupidatat non proident, sunt in culpa</p></div>
  <div class="abs why-item" style="left:311px;top:589px"><span class="dot"></span><h4>Lorem Ipsum</h4><p>Excepteur sint occaecat cupidatat non proident, sunt in culpa</p></div>
  <div class="abs why-item" style="left:195px;top:636px"><span class="dot"></span><h4>Lorem Ipsum</h4><p>Excepteur sint occaecat cupidatat non proident, sunt in culpa</p></div>
  <div class="abs why-item" style="left:311px;top:636px"><span class="dot"></span><h4>Lorem Ipsum</h4><p>Excepteur sint occaecat cupidatat non proident, sunt in culpa</p></div>
  <div class="abs why-btn"></div>
  <div class="abs photo-frame"></div>
  <div class="abs photo" role="img" aria-label="Mähdrescher bei der Getreideernte im Abendlicht"></div>
</section>

<section>
  <div class="abs badge badge-hupa" role="img" aria-label="HUPA Zertifikatssiegel"></div>
  <span class="abs und">und</span>
  <div class="abs badge-bt" role="img" aria-label="BT Zertifikatssiegel"></div>
  <span class="abs zert">zertifiziert</span>
  <div class="abs download">HERUNTERLADEN<br>ZERTIFIKAT</div>
  <div class="abs band-orange"></div>
</section>

<footer>
  <div class="abs foot-col" style="left:22px"><h5>Postanschrift</h5>Albtal Landhandel GbR<br>Lindenweg 4<br>91234 Mühlbach</div>
  <div class="abs foot-col" style="left:150px"><h5>Lieferanschrift</h5>Albtal Landhandel GbR<br>Wiesenstraße 7<br>91234 Mühlbach</div>
  <ul class="abs foot-col contact" style="left:270px;top:1009px">
    <li><svg width="11" height="11" viewBox="0 0 12 12"><circle cx="6" cy="6" r="6" fill="#f9ab25"/><path d="M3.5 3 L5 3 L5.5 5 L4.7 5.6 Q5.5 7.3 6.6 7.5 L7.2 6.8 L9 7.4 L9 8.8 Q5 9.2 3.5 4.5 Z" fill="#fff"/></svg>01234 56 78 90</li>
    <li><svg width="11" height="11" viewBox="0 0 12 12"><rect x="3" y="1" width="6" height="10" rx="1.2" fill="#f9ab25"/></svg>0150 123 45 67</li>
    <li><svg width="11" height="11" viewBox="0 0 12 12"><rect x="1" y="3" width="10" height="7" fill="#f9ab25"/><polyline points="1,3 6,7 11,3" fill="none" stroke="#fff" stroke-width="1"/></svg>Info@Albtal-Landhandel.De</li>
    <li><svg width="11" height="11" viewBox="0 0 12 12"><circle cx="6" cy="6" r="5" fill="none" stroke="#f9ab25" stroke-width="1.4"/><line x1="1" y1="6" x2="11" y2="6" stroke="#f9ab25"/><ellipse cx="6" cy="6" rx="2" ry="5" fill="none" stroke="#f9ab25"/></svg>Www.Albtal-Landhandel.De</li>
  </ul>
  <div class="abs foot-col" style="left:437px;top:1009px">Bankverbindung: Mühlbacher Landbank<br>IBAN: DE00 1234 5678 9012 3456 78<br>BIC: MUSTDEF1XXX<br>USt-IdNr.: DE000000000</div>
  <div class="abs mini-hupa" role="img" aria-label="HUPA Siegel"></div>
  <div class="abs mini-bt" role="img" aria-label="BT Siegel"></div>
  <p class="abs legal">Es Gelten Die Allgemeinen Lieferungs- Und Zahlungsbedingungen. Die Ware Bleibt Bis Zur Vollständigen Bezahlung<br>Unser Eigentum, Auch Bei Veräußerung, Verfütterung Oder Einer Weiteren Verwendung (Erweiterter Verlängerter Eigentumsvorbehalt).<br>Bei Verspäteter Zahlung Werden Übliche Verzugszinsen Berechnet. Gerichtsstand Ist Mühlbach</p>
  <div class="abs copy-bar">Copyright 2023 All Right Reserved</div>
</footer>

</body>
</html>
```